Wordpress site for cyber security and network perfomance software vendor

We need a brand new Wordpress website consisting of a single home/landing page and page template so that we can add pages in future.
The website is intended to provide information to prospects and customers. The homepage should have a top menu bar that is customizable similar to what we already have at quillmarsh.com.
Note that we are after a new design – that is, please don’t reference our existing website for design inspiration (quillmarsh.com)
We are after a Wordpress site that may be implemented straight onto our Wordpress hoster (HostPetal) .
Quillmarsh is a software company delivering a solution for customers to get visibility of network performance and cyber security. The Quillmarsh solution reduces cyber security risk, identifies performance bottlenecks and ultimately lower costs by reducing the number of tools need to monitor the IT environment
We deliver network performance and cyber security information to the IT manager and network teams in a format that they understand, at a realistic cost, and requiring minimal resource to implement. This is a crowded market, most competitors provide highly complex, expensive and highly customized tools to large enterprise. Quillmarsh makes this style of visibility tool accessible to the mid market.

Target Market(s)

IT Managers, network engineers, mid market organisations, IT service providers

Industry/Entity Type

IT

Font styles to use
Sans Serif

Colors
0094D4
00A9DD
6FCCEA
C7EBF8
E9F6FB

Requirements
Must have
• Fully coded for WordPress. Responsive and mobile friendly. The website copy is provided in the attached document. Utilise the Quillmarsh logo colors as part of the design (Dark Blue: 2E4F99, Light Blue: 00AFF4, Green: 73D94F). Top Horizontal menu bar for additional pages. Implement one of our screenshots (I have included a bunch of screenshots to choose from)
Nice to have
• Icons, panels or infographics matching the services. Our existing site is built using Divi – this is not a requirement for the new site but a nice to have as we are familiar with Divi.
Should not have
• Preferably no corporate images – business people shaking hands or teams of people a meeting room (or that kind of thing)

```html
<!DOCTYPE html>
<html lang="en">
<head>
<meta charset="utf-8">
<title>Quillmarsh – Security + Visibility</title>
<link href="https://fonts.googleapis.com/css2?family=Montserrat:wght@800;900&family=Poppins:wght@300;400;500&family=Roboto+Slab:wght@500&family=Rubik:wght@400;500&display=swap" rel="stylesheet">
<style>
:root{
  --navy:#0b3a7e;
  --navy-deep:#072c63;
  --ink:#111a2b;
  --blue:#1a9be6;
  --sky:#00afef;
  --green:#73cf4a;
  --green-deep:#55b93a;
  --mist:#e9f6fb;
  --text:#6a6f78;
  --line:#dfe5ec;
  --white:#fff;
}
*{margin:0;padding:0;box-sizing:border-box}
html,body{width:1200px;height:3412px;overflow:hidden}
body{position:relative;background:var(--white);font-family:"Poppins",sans-serif;color:var(--ink)}
.abs{position:absolute}
.deco{position:absolute;left:0;top:0;width:1200px;height:3412px}
/* header */
.brand{position:absolute;display:flex;align-items:center;gap:10px}
.brand-dot{width:44px;height:44px;border-radius:50%;background:var(--green)}
.brand-name{font-family:"Poppins",sans-serif;font-weight:400;font-size:30px;color:var(--navy)}
.nav{position:absolute;left:644px;top:20px;display:flex;align-items:center;gap:25px}
.nav a{color:#fff;text-decoration:none;font-size:13px;font-family:"Rubik",sans-serif}
.nav .login{background:#fff;color:var(--navy);padding:9px 19px;border-radius:4px;font-weight:500;margin-left:4px}
/* hero */
.hero-title{left:62px;top:228px;font-family:"Montserrat",sans-serif;font-weight:900;font-size:52px;line-height:60px;letter-spacing:1px;text-shadow:2px 3px 4px rgba(0,0,0,.15)}
.hero-title .l1{color:var(--navy)}
.hero-title .plus{color:var(--sky)}
.hero-title .l2{color:var(--green)}
.hero-sub{left:62px;top:388px;font-family:"Roboto Slab",serif;font-weight:500;font-size:14.5px;color:var(--navy)}
.btn-contact{left:60px;top:441px;width:118px;height:36px;border-radius:4px;background:var(--green);color:#fff;font-family:"Rubik",sans-serif;font-size:13px;display:flex;align-items:center;justify-content:center;box-shadow:0 4px 10px rgba(115,207,74,.35)}
.screen{background:linear-gradient(160deg,#2a2e35,#15181d);border-radius:4px}
/* headings */
.h-sec{width:1200px;left:0;text-align:center;font-family:"Rubik",sans-serif;font-weight:500;color:#000}
.h-sec em{font-style:normal;color:var(--blue)}
/* cards */
.card{width:248px;height:180px;border:1px solid var(--line);border-radius:4px;background:#fff;text-align:center;padding:62px 20px 0}
.card h3{font-family:"Rubik",sans-serif;font-weight:400;font-size:15px;margin-bottom:12px}
.card p{font-size:12.3px;line-height:19.5px;color:var(--text);font-weight:300}
.card-icon{position:absolute;left:90px;top:-35px;width:68px;height:68px;border-radius:50%;background:linear-gradient(135deg,var(--green),var(--sky));display:flex;align-items:center;justify-content:center}
/* bullets */
.bullets{left:645px;top:1200px;width:490px;list-style:none}
.bullets li{position:relative;padding-left:40px;font-size:12.3px;line-height:19.5px;color:var(--text);font-weight:300;margin-bottom:14px}
.bullets li::before{content:"";position:absolute;left:0;top:3px;width:13px;height:13px;border-radius:50%;border:3px solid var(--navy);background:#fff}
/* rings */
.ring-label{width:200px;text-align:center;font-family:"Rubik",sans-serif;font-size:18px;color:#000}
/* text blocks */
.h-side{font-family:"Rubik",sans-serif;font-weight:500;font-size:28px;color:#000}
.h-side em{font-style:normal;color:var(--blue)}
.copy p{font-size:12.3px;line-height:19.5px;color:var(--text);font-weight:300;margin-bottom:12px}
/* footer */
.foot-head{font-family:"Rubik",sans-serif;font-size:17px;color:#fff}
.sitemap{list-style:none}
.sitemap li{position:relative;padding-left:22px;font-size:12.5px;color:#fff;height:30px;line-height:16px}
.sitemap li::before{content:"";position:absolute;left:0;top:3px;width:9px;height:9px;border-radius:50%;border:2px solid var(--green)}
.social{display:flex;gap:9px}
.social span{width:29px;height:29px;border-radius:50%;background:#fff}
.call{display:flex;gap:14px;align-items:center}
.call-ic{width:40px;height:40px;border-radius:50%;border:1.5px solid rgba(255,255,255,.35);display:flex;align-items:center;justify-content:center}
.call small{display:block;color:var(--green);font-size:12px}
.call b{color:#fff;font-size:13px;font-weight:500}
.copyright{left:0;top:3375px;width:1200px;height:37px;background:linear-gradient(90deg,var(--green),var(--sky));color:#fff;font-size:12px;display:flex;align-items:center;justify-content:center}
</style>
</head>
<body>

<svg class="deco" viewBox="0 0 1200 3412" aria-hidden="true">
  <defs>
    <linearGradient id="gTop" x1="0" y1="0" x2="1" y2="0">
      <stop offset="0" stop-color="#73cf4a"/><stop offset=".55" stop-color="#1fb0d6"/><stop offset="1" stop-color="#0b5aa8"/>
    </linearGradient>
    <linearGradient id="gBand" x1="0" y1="0" x2="1" y2="1">
      <stop offset="0" stop-color="#73cf4a"/><stop offset="1" stop-color="#00afef"/>
    </linearGradient>
    <linearGradient id="gMist" x1="0" y1="0" x2="0" y2="1">
      <stop offset="0" stop-color="#d6ecf8"/><stop offset="1" stop-color="#eef7fc"/>
    </linearGradient>
  </defs>
  <!-- hero dark sweep -->
  <path d="M585 115 C700 100 1000 80 1200 90 L1200 530 C1150 520 1110 470 1100 380 C1080 250 850 160 585 115Z" fill="#0b3a7e"/>
  <!-- hero gradient blob -->
  <path d="M460 0 L1200 0 L1200 80 C1020 120 800 125 640 110 C520 100 470 60 460 0Z" fill="url(#gTop)"/>
  <!-- mist band -->
  <path d="M0 1020 C250 1040 480 1090 600 1080 C800 1060 960 1060 1040 1150 C1100 1250 1000 1450 860 1560 C700 1640 400 1640 0 1620Z" fill="url(#gMist)" opacity=".8"/>
  <!-- faint ring decoration right -->
  <circle cx="1080" cy="2420" r="90" fill="none" stroke="#e6f3f8" stroke-width="28"/>
  <circle cx="1120" cy="2230" r="40" fill="#eef7f1"/>
  <!-- photo band -->
  <path d="M150 2440 C160 2425 175 2420 200 2422 L500 2460 C530 2464 545 2480 548 2500 L548 2855 C548 2870 530 2862 500 2858 L140 2815 Z" fill="url(#gBand)"/>
  <!-- footer wave -->
  <path d="M0 3150 C40 3060 130 3030 260 3000 C420 2965 560 2960 700 2930 C850 2900 950 2890 1060 2895 C1140 2900 1190 2960 1200 2990 L1200 3412 L0 3412 Z" fill="#0b3a7e"/>
  <path d="M0 3260 C200 3190 500 3180 760 3230 C960 3270 1120 3250 1200 3210 L1200 3412 L0 3412Z" fill="#072c63" opacity=".55"/>
</svg>

<!-- header -->
<div class="brand" style="left:60px;top:24px"><span class="brand-dot"></span><span class="brand-name">Quillmarsh</span></div>
<nav class="nav">
  <a>Home</a><a>Product</a><a>Blog</a><a>About</a><a>Partner Portal</a><a class="login">DEMO LOGIN</a>
</nav>

<!-- hero -->
<h1 class="abs hero-title"><span class="l1">SECURITY </span><span class="plus">+</span><br><span class="l2">VISIBILITY</span></h1>
<p class="abs hero-sub">Network Monitoring for IT Perfowmance and Security</p>
<div class="abs btn-contact">CONTACT US</div>
<div class="abs screen" style="left:607px;top:170px;width:527px;height:353px" role="img" aria-label="Dashboard screenshot showing network throughput chart and application distribution donut charts"></div>

<!-- services -->
<h2 class="abs h-sec" style="top:624px;font-size:28px">We deliver everything <em>you need</em></h2>
<div class="abs card" style="left:60px;top:730px"><div class="card-icon"><svg width="32" height="32" viewBox="0 0 32 32" fill="none" stroke="#fff" stroke-width="2"><rect x="4" y="6" width="24" height="16" rx="2"/><path d="M8 18l5-5 4 3 6-6"/></svg></div><h3>Sophisticated Data Analytics</h3><p>Powerful data analytics correlate threat data and anomalous traffic data with network performance</p></div>
<div class="abs card" style="left:338px;top:730px"><div class="card-icon"><svg width="32" height="32" viewBox="0 0 32 32" fill="none" stroke="#fff" stroke-width="2"><rect x="5" y="5" width="22" height="16" rx="2"/><path d="M10 21v6M22 21v6M9 16l5-4 4 3 5-5"/></svg></div><h3>Best Visual Analytics</h3><p>Proactive alerts and dynamic traffic flows are integrated into an intuitive, user friendly dashboard that</p></div>
<div class="abs card" style="left:615px;top:730px"><div class="card-icon"><svg width="32" height="32" viewBox="0 0 32 32" fill="none" stroke="#fff" stroke-width="2"><circle cx="16" cy="16" r="6"/><path d="M16 3v5M16 24v5M3 16h5M24 16h5M7 7l3 3M22 22l3 3M25 7l-3 3M7 25l3-3"/></svg></div><h3>Flexible Solutions</h3><p>Our network monitoring AND cyber security solution can be scaled to fit your organisation.</p></div>
<div class="abs card" style="left:893px;top:730px"><div class="card-icon"><svg width="32" height="32" viewBox="0 0 32 32" fill="none" stroke="#fff" stroke-width="2"><path d="M8 5h16l5 7-13 15L3 12z"/><path d="M3 12h26M12 5l4 22 4-22"/></svg></div><h3>Superior Service</h3><p>From first contact through to deployment, our friendly, expert team will discuss your needs and.</p></div>

<!-- specialising -->
<h2 class="abs h-sec" style="top:990px;font-size:29px;line-height:37px">Specialising in IT Network Performance and<br>Cyber Security Solutions for S<em>mall to Medium</em><br><em>Organisations.</em></h2>
<div class="abs screen" style="left:66px;top:1139px;width:526px;height:287px;border:3px solid #000;box-shadow:0 4px 10px rgba(0,0,0,.3)" role="img" aria-label="Dashboard screenshot showing packet arrival time chart and best and worst performing apps and hosts"></div>
<ul class="abs bullets">
  <li>Do you feel concerned about your network performance, and cyber threats, but you don't have the time or staff to deal with it?</li>
  <li>Perhaps you've outsourced your IT support and have discovered that your service provider doesn't have visibility of your network?</li>
  <li>It's not easy being an IT manager. Especially if you work in a small to medium sized organisation. You're typically stretched to the limit with an understaffed team and there's simply not enough hours in the day to tackle all the increasing demands.</li>
</ul>

<!-- committed -->
<h2 class="abs h-sec" style="top:1514px;font-size:29px;line-height:38px">we’re committed to providing you the <em>best</em><br><em>easy-to-use tools</em></h2>
<svg class="abs" style="left:172px;top:1634px" width="152" height="152" viewBox="0 0 152 152" fill="none" stroke-width="13">
  <path d="M76 8a68 68 0 0 1 62 40" stroke="#0b3a7e"/><path d="M144 76a68 68 0 0 1-48 65" stroke="#0b3a7e"/><path d="M56 141A68 68 0 0 1 8 76" stroke="#0b3a7e"/><path d="M14 48A68 68 0 0 1 48 14" stroke="#0b3a7e"/>
  <path d="M38 76c20-26 56-26 76 0-20 26-56 26-76 0z" stroke="#1a9be6" stroke-width="4"/><circle cx="76" cy="76" r="12" stroke="#1a9be6" stroke-width="5"/>
</svg>
<svg class="abs" style="left:524px;top:1634px" width="152" height="152" viewBox="0 0 152 152" fill="none" stroke-width="13">
  <path d="M76 8a68 68 0 0 0-62 40" stroke="#55c06a"/><path d="M8 76a68 68 0 0 0 48 65" stroke="#3cb6a6"/><path d="M96 141A68 68 0 0 0 144 76" stroke="#1aa8d6"/><path d="M138 48A68 68 0 0 0 104 14" stroke="#1a9be6"/>
  <circle cx="72" cy="72" r="22" stroke="#1a9be6" stroke-width="3"/><circle cx="72" cy="72" r="13" stroke="#1a9be6" stroke-width="3"/><rect x="80" y="86" width="16" height="12" rx="2" fill="#0b3a7e" stroke="none"/>
</svg>
<svg class="abs" style="left:862px;top:1634px" width="152" height="152" viewBox="0 0 152 152" fill="none" stroke-width="13">
  <path d="M76 8a68 68 0 0 1 62 40" stroke="#0b3a7e"/><path d="M144 76a68 68 0 0 1-48 65" stroke="#0b3a7e"/><path d="M56 141A68 68 0 0 1 8 76" stroke="#0b3a7e"/><path d="M14 48A68 68 0 0 1 48 14" stroke="#0b3a7e"/>
  <path d="M56 84c-8-6-8-26 8-30 8-10 26-8 30 2 12 2 12 20 2 24v12H70v-8z" stroke="#1a9be6" stroke-width="3"/><path d="M66 66h14l6 8M74 58v10" stroke="#1a9be6" stroke-width="2"/>
</svg>
<div class="abs ring-label" style="left:134px;top:1808px">Visibility</div>
<div class="abs ring-label" style="left:496px;top:1808px">security</div>
<div class="abs ring-label" style="left:841px;top:1808px">peace of mind</div>

<!-- why -->
<h2 class="abs h-side" style="left:61px;top:1928px">Why <em>Quillmarsh ?</em></h2>
<div class="abs copy" style="left:61px;top:1984px;width:420px">
  <p>At Quillmarsh, we understand the challenges that you face. Cyber security and network incidents can have devastating impacts on small to medium organisations because you typically don't have the time, staff, or resources to develop complicated responses to cyber security threats</p>
  <p>That's why small to medium sized organisations are vulnerable to potentially devastating cyber incidents. Did you know that on average, it took over 220 days for organisations to identify a breach and a further 80 days to contain the breach? (Larkfield Research, 2020).</p>
  <p>With Quillmarsh, you can avoid these unpleasant surprises.</p>
  <p>We're committed to providing the best easy-to-use cyber tools for small to medium organisations that will give you visibility across your network, performance, AND cyber security data. So, you won't get any nasty surprises.</p>
</div>
<div class="abs" style="left:750px;top:1925px;width:362px;height:362px;border-radius:50%;border:1.5px solid #73cf4a"></div>
<div class="abs" style="left:757px;top:1931px;width:353px;height:353px;border-radius:50%;background:radial-gradient(circle at 40% 60%,#2a8fd0,#0d3a73 70%)" role="img" aria-label="Photo of hands typing on a laptop beneath a digital security shield"></div>
<div class="abs" style="left:762px;top:2140px;width:140px;height:140px;border-radius:50%;border:14px solid #0b3a7e;opacity:.85"></div>

<!-- no obligations -->
<div class="abs" style="left:60px;top:2510px;width:525px;height:298px;border-radius:8px;background:linear-gradient(135deg,#f0b37a,#8c5a3c 60%,#3b2c2a)" role="img" aria-label="Photo of hands typing on a laptop with glowing security padlock icons"></div>
<h2 class="abs h-side" style="left:616px;top:2566px">No <em>obligations</em></h2>
<div class="abs copy" style="left:616px;top:2618px;width:440px">
  <p>At Quillmarsh, we have designed a network performance monitoring and cyber security visibility solution that is both simple and comprehensive, that is, simple to install yet comprehensive in the functionality and benefit to your business.&nbsp; In the simplest form there are 2 components, an appliance which isn't installed on site and collects statistical information and continuously listens out for malicious activity, and a web based reporting dashboard living in the cloud that presents the information in a clear and concise format.</p>
</div>

<!-- footer -->
<div class="abs foot-head" style="left:0;width:1680px;text-align:center;top:2998px;font-size:21px;font-weight:500">We would love to hear from you.</div>
<div class="abs foot-head" style="left:196px;top:3080px">Site Map</div>
<ul class="abs sitemap" style="left:196px;top:3116px">
  <li>Home</li><li>About Us</li><li>Product</li><li>Blog</li><li>About Us</li><li>Partner Portal</li><li>Demo Login</li>
</ul>
<div class="brand" style="left:512px;top:3082px"><span class="brand-dot" style="background:var(--sky)"></span><span class="brand-name" style="color:#fff">Quillmarsh</span></div>
<div class="abs social" style="left:544px;top:3162px"><span></span><span></span><span></span></div>
<div class="abs foot-head" style="left:870px;top:3080px">Give us a call!</div>
<div class="abs call" style="left:862px;top:3120px">
  <span class="call-ic"><svg width="18" height="18" viewBox="0 0 24 24" fill="none" stroke="#73cf4a" stroke-width="2"><path d="M5 3h4l2 5-3 2a11 11 0 0 0 6 6l2-3 5 2v4a2 2 0 0 1-2 2A17 17 0 0 1 3 5a2 2 0 0 1 2-2z"/></svg></span>
  <div><small>Australia</small><b>+61 2 5550 1234</b></div>
</div>
<div class="abs call" style="left:862px;top:3187px">
  <span class="call-ic"><svg width="18" height="18" viewBox="0 0 24 24" fill="none" stroke="#73cf4a" stroke-width="2"><path d="M5 3h4l2 5-3 2a11 11 0 0 0 6 6l2-3 5 2v4a2 2 0 0 1-2 2A17 17 0 0 1 3 5a2 2 0 0 1 2-2z"/></svg></span>
  <div><small>Germany</small><b>+49 30 555 01 876</b></div>
</div>
<div class="abs copyright">Copyright Quillmarsh 2020- All Right Resrved.</div>

</body>
</html>
```